"Velmora Crest" sexual performance enhancement pill bottle label needed.

This should be interesting...

I am starting a line of sexual performance enhancement products. This will be the first of several products basically. Keep in mind, I am the type of business person to stay with one company for years if they provide me with quality work.

This particular product is a male sexual performance pill. The name of the product is "Velmora Crest." The packaging of the pills are a black bottle with a white top. Label on the product example would be perfect but at a minimum I have attached a "template" for your guidance.

Some of the technical aspects of this are as follows:

-File Format: Illustrator CS6 is preferred. (Winner must provide artwork in layer and can not flatten artwork.)
-Resolution: 300 dpi minimum
-Bleed: 1/16th (0.0625") inch from edge of label
-Color Mode: CMYK only or must be converted to CMYK for final production

Lastly, this is your project as a designer, artist, creator, this is essentially a piece of you that will be sold and known by thousands of people. I have no color scheme that I prefer, just use the template and follow the layout. If you have any further questions, please feel free to contact me at any time.
Updates

Quick note on the product and what it does: -Powerful, long lasting, harder erections -Works in a minutes and last for hours -Enhances sexual desire and drive Thank you for your ideas...

Project Deadline Extended
Reason: We decided to extent the project for a few more days to let the last few concepts come in. So far things are looking really good and we definitely have seen some amazing designs. Thank you for your hard work and amazing creativity. Looking forward to seeing what we have come in the next couple of day. Very respectfully, Brev

ONLY THREE DAYS LEFT!!!! Please submit your ideas as soon as possible. And as always, thank you for your help!!! V/r, Brev

Industry/Entity Type

Graphic Design

```html
<!DOCTYPE html>
<html lang="en">
<head>
<meta charset="utf-8">
<title>Velmora Crest – Horny Goat Weed 1600 Label</title>
<link rel="stylesheet" href="https://fonts.googleapis.com/css2?family=Dosis:wght@300;400&family=Ubuntu:wght@400;700&display=swap">
<style>
  :root {
    --stage: #2b2b2b;
    --label: #0b0b0b;
    --label-edge: #1c1c1c;
    --title-grey: #9b9b9b;
    --muted-grey: #7d7d7d;
    --soft-white: #d9d9d9;
    --white: #ffffff;
    --fine-print: #6a6a6a;
  }
  * { margin: 0; padding: 0; box-sizing: border-box; }
  html, body {
    width: 1200px;
    height: 900px;
    overflow: hidden;
    background: var(--stage);
  }
  .canvas {
    position: relative;
    width: 1200px;
    height: 900px;
    display: flex;
    align-items: center;
    justify-content: center;
  }
  .label {
    position: relative;
    width: 980px;
    height: 420px;
    background: var(--label);
    border: 1px solid var(--label-edge);
    display: grid;
    grid-template-columns: 250px 1fr 250px;
  }
  .side-panel {
    padding: 48px 30px;
    font-family: "Ubuntu", sans-serif;
    font-size: 11px;
    line-height: 1.55;
    color: var(--fine-print);
  }
  .side-panel--left { border-right: 1px solid var(--label-edge); }
  .side-panel--right { border-left: 1px solid var(--label-edge); }
  .side-panel strong { color: var(--muted-grey); }
  .footnote { margin-top: 16px; font-size: 10px; }
  .front-panel {
    display: flex;
    flex-direction: column;
    align-items: center;
    text-align: center;
    padding-top: 52px;
  }
  .product-title {
    font-family: "Dosis", sans-serif;
    font-weight: 300;
    font-size: 42px;
    line-height: 1.05;
    color: var(--title-grey);
    letter-spacing: 0.5px;
  }
  .brand-name {
    margin-top: 40px;
    font-family: "Ubuntu", sans-serif;
    font-weight: 700;
    font-size: 38px;
    line-height: 1.0;
    color: var(--white);
    letter-spacing: 1px;
    text-transform: uppercase;
  }
  .tagline {
    margin-top: 12px;
    font-family: "Ubuntu", sans-serif;
    font-size: 15px;
    color: var(--muted-grey);
  }
  .claim {
    margin-top: 52px;
    font-family: "Ubuntu", sans-serif;
    font-size: 15px;
    color: var(--white);
  }
  .claim sup { font-size: 10px; }
  .contents {
    margin-top: 12px;
    font-family: "Ubuntu", sans-serif;
    font-size: 14px;
    color: var(--soft-white);
  }
</style>
</head>
<body>
  <main class="canvas">
    <section class="label">
      <aside class="side-panel side-panel--left">
        <p><strong>Directions:</strong> As a dietary supplement, take two capsules daily with water, preferably with a meal. Do not exceed the suggested use.</p>
        <p class="footnote">*These statements have not been evaluated by the Food and Drug Administration.</p>
      </aside>

      <div class="front-panel">
        <h1 class="product-title">Horny Goat Weed<br>1600</h1>
        <p class="brand-name">Velmora<br>Crest</p>
        <p class="tagline">Max Strength!</p>
        <p class="claim">Pure and Potent<sup>*</sup></p>
        <p class="contents">Dietary Supplement · 60 Capsules</p>
      </div>

      <aside class="side-panel side-panel--right">
        <p><strong>Warning:</strong> Consult your physician before use if you are taking medication or have a medical condition. Keep out of reach of children. Store in a cool, dry place.</p>
      </aside>
    </section>
  </main>
</body>
</html>
```